Flyer for the Lumen 2025 Conference

I am looking to produce a flyer for our upcoming conference, Lumen 2025. This is an annual conference that we plan to publicize on social media. The ideal designer will create a flyer that is eye-catching and effectively communicates the key information. Please see attached our logo, speaker photo, and flyer content.

Target Market(s)

All demographics

Industry/Entity Type

Christian

Font styles to use
Sans Serif

Requirements
Should not have
• Cross, church

```html
<!DOCTYPE html>
<html lang="en">
<head>
<meta charset="utf-8">
<title>Lumen 2025 Conference</title>
<link rel="stylesheet" href="https://fonts.googleapis.com/css2?family=Anton&family=Great+Vibes&family=Montserrat:wght@500;600;700;800&family=Oswald:wght@500;600&display=swap">
<style>
:root{
  --stage:#cbcbcd;
  --navy-deep:#07081a;
  --navy:#1a1f5e;
  --royal:#2b3aa6;
  --orange:#f7a51d;
  --orange-deep:#e0651c;
  --teal:#4cc3cf;
  --white:#ffffff;
  --box:#0a0c24;
}
*{margin:0;padding:0;box-sizing:border-box}
html,body{width:911px;height:1200px;overflow:hidden;background:var(--stage)}
.flyer{
  position:absolute;left:91px;top:85px;width:728px;height:1030px;overflow:hidden;
  background:
    linear-gradient(180deg,rgba(0,0,0,0) 55%,#000 92%),
    linear-gradient(100deg,var(--navy-deep) 0%,var(--navy) 45%,var(--royal) 100%);
  font-family:"Montserrat",sans-serif;color:var(--white);
}
.speaker-photo{position:absolute;left:0;top:197px;width:440px;height:833px;
  background:radial-gradient(closest-side at 40% 45%,#2f6fc4 0%,#1d4f9e 45%,rgba(10,20,60,0) 100%)}
.speaker-photo-faded{position:absolute;left:470px;top:94px;width:258px;height:760px;opacity:.5;
  background:radial-gradient(closest-side at 50% 40%,#2a3488 0%,rgba(20,25,80,0) 100%)}
.topic{position:absolute;left:39px;top:48px;font-size:19px;font-weight:600;line-height:21px}
.label{color:var(--orange);font-weight:800}
.speaker{position:absolute;right:35px;top:48px;text-align:right;font-size:19px;font-weight:600;line-height:21px}
.brand{position:absolute;left:250px;top:72px;width:234px;display:flex;align-items:center;justify-content:center;gap:8px;
  font-size:40px;font-weight:600;letter-spacing:1px;color:var(--white);line-height:48px}
.brand-dot{width:14px;height:14px;border-radius:50%;background:var(--orange)}
.headline{position:absolute;left:200px;top:160px}
.dates{position:absolute;left:154px;top:582px;display:flex;gap:23px}
.date-card{width:125px;height:170px;border:2px solid var(--orange);background:var(--box);
  display:flex;flex-direction:column;align-items:center;padding-top:12px}
.date-month{font-family:"Oswald",sans-serif;font-weight:500;font-size:22px;line-height:24px;color:var(--teal)}
.date-day{font-family:"Oswald",sans-serif;font-weight:500;font-size:50px;line-height:48px;color:var(--white);margin-top:2px}
.date-weekday{font-weight:800;font-size:21px;line-height:22px;color:var(--orange)}
.date-weekday.small{font-size:17px}
.time{position:relative;margin-top:4px;width:88px}
.time-start,.time-end{display:block;height:19px;line-height:19px;text-align:center;font-weight:700;font-size:15px;color:var(--white)}
.time-start{background:var(--orange)}
.time-end{background:var(--teal);margin-top:5px}
.time-to{position:absolute;left:50%;top:15.5px;transform:translateX(-50%);width:11px;height:11px;border-radius:50%;
  background:var(--white);color:#000;font-size:5px;font-weight:800;line-height:11px;text-align:center}
.app{position:absolute;left:464px;top:822px;font-size:15px;font-weight:500;line-height:19px}
.app-name{font-size:21px;font-weight:800;color:var(--orange);line-height:24px}
.stores{display:flex;gap:8px;margin-top:9px}
.store-badge{width:82px;height:25px;border-radius:5px;background:var(--white)}
.contacts{position:absolute;left:464px;top:934px;list-style:none;font-size:15px;font-weight:500}
.contacts li{display:flex;align-items:center;gap:8px;height:21px}
.contacts svg{width:17px;height:17px;flex:none}
.location{position:absolute;left:29px;top:895px}
.location-title{font-family:"Great Vibes",cursive;font-size:44px;color:var(--orange);line-height:50px}
.venue{font-size:15px;font-weight:800;line-height:19px}
.address{font-size:15px;font-weight:500;line-height:19px}
</style>
</head>
<body>
<main class="flyer">
  <div class="speaker-photo-faded" role="img" aria-label="Faded portrait of the speaker in the background"></div>
  <div class="speaker-photo" role="img" aria-label="Seated portrait of the speaker in a blue suit and grey turtleneck"></div>

  <div class="topic"><span class="label">TOPIC:</span><br>THE VOICE<br>OF THE LORD</div>
  <div class="speaker"><span class="label">SPEAKER:</span><br>PROPHET<br>SAMUEL ADEYO</div>

  <div class="brand"><span class="brand-dot"></span>HALVORA</div>

  <svg class="headline" width="330" height="400" viewBox="0 0 330 400">
    <defs>
      <linearGradient id="fire" x1="0" y1="0" x2="1" y2="1">
        <stop offset="0" stop-color="#d4541a"/>
        <stop offset=".5" stop-color="#f08e22"/>
        <stop offset="1" stop-color="#f7a51d"/>
      </linearGradient>
    </defs>
    <text x="6" y="113" font-family="Anton, sans-serif" font-size="137" fill="url(#fire)" textLength="304" lengthAdjust="spacingAndGlyphs">LUMEN</text>
    <text x="8" y="270" font-family="Anton, sans-serif" font-size="177" fill="#fff" textLength="313" lengthAdjust="spacingAndGlyphs">2025</text>
    <text x="5" y="350" font-family="Anton, sans-serif" font-size="66" fill="#4cc3cf" textLength="314" lengthAdjust="spacingAndGlyphs">A PROPHETIC</text>
    <text x="3" y="396" font-family="Montserrat, sans-serif" font-weight="600" font-size="44" fill="#fff" textLength="312" lengthAdjust="spacingAndGlyphs">CONFERENCE</text>
  </svg>

  <section class="dates">
    <div class="date-card">
      <span class="date-month">DECEMBER</span>
      <span class="date-day">26TH</span>
      <span class="date-weekday">FRIDAY</span>
      <div class="time"><span class="time-start">6:30 PM</span><span class="time-to">TO</span><span class="time-end">9:00 PM</span></div>
    </div>
    <div class="date-card">
      <span class="date-month">DECEMBER</span>
      <span class="date-day">27TH</span>
      <span class="date-weekday small">SATURDAY</span>
      <div class="time"><span class="time-start">5:30 PM</span><span class="time-to">TO</span><span class="time-end">8:00 PM</span></div>
    </div>
    <div class="date-card">
      <span class="date-month">DECEMBER</span>
      <span class="date-day">29TH</span>
      <span class="date-weekday">SUNDAY</span>
      <div class="time"><span class="time-start">4:30 PM</span><span class="time-to">TO</span><span class="time-end">7:00 PM</span></div>
    </div>
  </section>

  <section class="app">
    <div>Download the</div>
    <div class="app-name">HALVORA APP</div>
    <div>to stay updated on the event</div>
    <div class="stores"><span class="store-badge"></span><span class="store-badge"></span></div>
  </section>

  <ul class="contacts">
    <li><svg viewBox="0 0 20 20"><circle cx="10" cy="10" r="10" fill="#f7a51d"/><rect x="7" y="4.5" width="6" height="11" rx="1" fill="none" stroke="#07081a" stroke-width="1.3"/></svg>207 555 0142</li>
    <li><svg viewBox="0 0 20 20"><circle cx="10" cy="10" r="10" fill="#f7a51d"/><rect x="5" y="6.5" width="10" height="7" rx="1" fill="none" stroke="#07081a" stroke-width="1.2"/><path d="M5 7l5 4 5-4" fill="none" stroke="#07081a" stroke-width="1.2"/></svg>contact@halvora.org</li>
    <li><svg viewBox="0 0 20 20"><circle cx="10" cy="10" r="10" fill="#f7a51d"/><circle cx="10" cy="10" r="5.5" fill="none" stroke="#07081a" stroke-width="1.2"/><path d="M4.5 10h11M10 4.5c-3 3-3 8 0 11M10 4.5c3 3 3 8 0 11" fill="none" stroke="#07081a" stroke-width="1"/></svg>www.halvora.org</li>
  </ul>

  <section class="location">
    <div class="location-title">Location</div>
    <div class="venue">The Harborview Performing Arts Hall</div>
    <div class="address">318 Linden Street Brookhaven, Maine 04107</div>
  </section>
</main>
</body>
</html>
```